Executive Business Card for Healthcare Company [Need Today]

I need a business card design for a healthcare company. The only branding the company has thus far is a logo. The cards will be utilized by company executives. The design I envision will be vibrant and appealing but with a corporate feel. They shouldn't be too casual or playful. I would like to complete this project TODAY if possible.

Target Market(s)

Healthcare vendors, other executives in healthcare and pharmaceuticals

Industry/Entity Type

Pharmaceutical

Contact Information for Business Card

See attachment

Font styles to use
Serif
Sans Serif

Colors

Designer to choose colors to be used in the design.

```html
<!DOCTYPE html>
<html lang="en">
<head>
<meta charset="utf-8">
<title>Ardela Therapeutics — Business Card</title>
<link rel="stylesheet" href="https://fonts.googleapis.com/css2?family=Roboto:wght@300;400;500&display=swap">
<style>
  :root {
    --backdrop: #3b3b3d;
    --card: #202022;
    --teal: #27b3c4;
    --mint: #3cc0a0;
    --ink: #e9e9ea;
    --ink-soft: #cfcfd1;
  }
  * { box-sizing: border-box; margin: 0; padding: 0; }
  html, body { width: 799px; height: 1200px; overflow: hidden; }
  body {
    background: var(--backdrop);
    font-family: "Roboto", Arial, sans-serif;
    color: var(--ink);
    position: relative;
  }
  .card {
    position: absolute;
    left: 80px;
    width: 640px;
    height: 366px;
    background: var(--card);
    border-radius: 4px;
    overflow: hidden;
    box-shadow: 0 14px 30px rgba(0,0,0,.45);
  }
  .card--front { top: 130px; }
  .card--back { top: 710px; }

  /* Front */
  .front-brand {
    position: absolute;
    left: 90px; top: 118px;
    display: flex; align-items: center; gap: 22px;
  }
  .brand-dot {
    width: 96px; height: 96px;
    border: 3px solid var(--mint);
    border-radius: 50%;
  }
  .brand-divider { width: 1px; height: 78px; background: var(--ink-soft); }
  .brand-name {
    font-weight: 300;
    color: var(--teal);
    line-height: 1.05;
  }
  .front-brand .brand-name { font-size: 40px; }
  .front-url {
    position: absolute;
    left: 90px; bottom: 52px;
    font-size: 15px; letter-spacing: 4px;
    color: var(--ink);
  }

  /* Back */
  .back-ring {
    position: absolute;
    left: -150px; top: -20px;
    width: 360px; height: 360px;
    border: 6px solid var(--mint);
    border-radius: 50%;
  }
  .back-edge {
    position: absolute;
    right: -22px; top: 232px;
    width: 44px; height: 60px;
    background: var(--mint);
    border-radius: 50%;
  }
  .back-brand {
    position: absolute;
    right: 50px; top: 54px;
    text-align: right;
  }
  .back-brand .brand-name { font-size: 38px; }
  .person {
    position: absolute;
    right: 50px; top: 150px;
    text-align: right;
  }
  .person-name { font-size: 24px; font-weight: 500; color: var(--teal); }
  .person-role { font-size: 12px; color: var(--ink-soft); margin-top: 3px; }
  .contact {
    position: absolute;
    right: 50px; top: 222px;
    list-style: none;
    text-align: right;
    font-size: 15px; line-height: 21px;
  }
  .contact li { display: flex; justify-content: flex-end; align-items: center; gap: 8px; }
  .contact svg { width: 13px; height: 13px; fill: none; stroke: var(--teal); stroke-width: 2; }
  .contact .spacer { width: 13px; }
</style>
</head>
<body>
  <section class="card card--front">
    <div class="front-brand">
      <div class="brand-dot"></div>
      <div class="brand-divider"></div>
      <div class="brand-name">Ardela<br>Therapeutics</div>
    </div>
    <p class="front-url">www.ardelarx.com</p>
  </section>

  <section class="card card--back">
    <div class="back-ring"></div>
    <div class="back-edge"></div>
    <div class="back-brand">
      <div class="brand-name">Ardela Therapeutics</div>
    </div>
    <div class="person">
      <p class="person-name">Daniel Mercer</p>
      <p class="person-role">Senior Director of Marketing</p>
    </div>
    <ul class="contact">
      <li>555-014-2287
        <svg viewBox="0 0 16 16"><path d="M4 2l2 3-1.5 1.5a8 8 0 0 0 5 5L11 10l3 2-1.5 2.5C7 14 2 9 1.5 3.5z"/></svg>
      </li>
      <li>555-019-4436
        <svg viewBox="0 0 16 16"><rect x="4" y="1.5" width="8" height="13" rx="1.5"/><path d="M7 12h2"/></svg>
      </li>
      <li>dmercer@ardelarx.com
        <svg viewBox="0 0 16 16"><circle cx="8" cy="8" r="6.5"/><path d="M1.5 8h13M8 1.5c-3 3.5-3 9.5 0 13M8 1.5c3 3.5 3 9.5 0 13"/></svg>
      </li>
      <li>118 N Laurel Avenue Dayton, OH 45402 <span class="spacer"></span></li>
    </ul>
  </section>
</body>
</html>
```